Business Card Design for Marketing Firm

Looking for business card design for higher end marketing firm. Clean but impressionable/trendy. We are a marketing firm that represents manufacturers in the foodservice equipment and supply industry. Our customers are end users such has hotels, restaurants, country clubs, convention centers and casinos as well as distributors of restaurants supplies and equipment, and manufacturers of foodservice equipment and supplies.
Target Market(s)
Hotels, Restaurants, Supply & Equipment Distributors, Foodservice Manufacturers
Industry/Entity Type
Foodservice/Hospitality
Contact Information for Business Card
Name, Title, Contact Number, Email, Website, Social Media, Address
Requirements
Must have
- Clean & Simple but Serious and Impressionable

```html
<!DOCTYPE html>
<html lang="en">
<head>
<meta charset="utf-8">
<title>Meridian Service Reps — Business Card</title>
<link rel="stylesheet" href="https://fonts.googleapis.com/css2?family=Open+Sans:wght@400;600;700&display=swap">
<style>
  :root {
    --navy: #282a78;
    --white: #ffffff;
    --backdrop: #eceae6;
  }
  * { box-sizing: border-box; margin: 0; padding: 0; }
  html, body {
    width: 1200px; height: 834px; overflow: hidden;
    background: var(--backdrop);
    font-family: "Open Sans", Arial, sans-serif;
  }
  .sheet {
    width: 1200px; height: 834px;
    display: flex; align-items: center; justify-content: center; gap: 40px;
  }
  .card {
    position: relative;
    width: 560px; height: 320px;
    border-radius: 28px;
    background: var(--white);
    overflow: hidden;
    box-shadow: 0 6px 18px rgba(0,0,0,.12);
  }
  .card-shape { position: absolute; inset: 0; }

  /* Contact side */
  .person { position: absolute; left: 34px; top: 112px; color: var(--white); }
  .person-name { font-weight: 700; font-size: 21px; letter-spacing: .5px; line-height: 1.2; }
  .person-title { font-size: 13px; margin-top: 2px; }
  .divider {
    position: absolute; left: 190px; top: 190px;
    width: 1px; height: 58px; background: var(--white);
  }
  .contact-list {
    position: absolute; left: 202px; top: 192px;
    list-style: none; color: var(--white); font-size: 12px; line-height: 18px;
  }
  .contact-list li { display: flex; align-items: center; gap: 6px; white-space: nowrap; }
  .contact-list svg { width: 10px; height: 10px; fill: var(--white); flex: none; }
  .address {
    position: absolute; left: 34px; top: 272px;
    color: var(--white); font-size: 13px;
  }

  /* Company name lockup */
  .wordmark {
    color: var(--navy);
    font-weight: 600;
    text-transform: uppercase;
    text-align: right;
    line-height: 1.05;
    white-space: nowrap;
  }
  .wordmark-main { display: block; padding-bottom: 4px; border-bottom: 1.5px solid var(--navy); }
  .wordmark-sub { display: block; padding-top: 3px; }
  .card-contact .wordmark {
    position: absolute; left: 300px; top: 52px; font-size: 19px;
  }

  .card-brand .wordmark {
    position: absolute; left: 50%; top: 118px; transform: translateX(-50%);
    font-size: 31px;
  }
  .social-row {
    position: absolute; left: 50%; top: 212px; transform: translateX(-50%);
    display: flex; gap: 8px; list-style: none;
  }
  .social-row li {
    width: 16px; height: 16px; border-radius: 50%; background: var(--navy);
  }
</style>
</head>
<body>
<main class="sheet">

  <section class="card card-contact" aria-label="Business card, contact side">
    <svg class="card-shape" viewBox="0 0 560 320" preserveAspectRatio="none" aria-hidden="true">
      <path d="M0 0 H100 C120 110 220 170 560 215 V320 H0 Z" fill="var(--navy)"/>
      <path d="M112 4 C132 106 232 160 556 202" fill="none" stroke="var(--navy)" stroke-width="1.6"/>
    </svg>

    <div class="wordmark">
      <span class="wordmark-main">Meridian Service</span>
      <span class="wordmark-sub">Reps</span>
    </div>

    <div class="person">
      <p class="person-name">DANIEL HART</p>
      <p class="person-title">Managing Director</p>
    </div>
    <span class="divider"></span>
    <ul class="contact-list">
      <li>
        <svg viewBox="0 0 24 24" aria-hidden="true"><path d="M6.6 10.8a15 15 0 0 0 6.6 6.6l2.2-2.2a1 1 0 0 1 1-.25 11.4 11.4 0 0 0 3.6.57 1 1 0 0 1 1 1V20a1 1 0 0 1-1 1A17 17 0 0 1 3 4a1 1 0 0 1 1-1h3.5a1 1 0 0 1 1 1c0 1.25.2 2.45.57 3.57a1 1 0 0 1-.25 1z"/></svg>
        123 456 789
      </li>
      <li>
        <svg viewBox="0 0 24 24" aria-hidden="true"><path d="M2 5h20v14H2z"/></svg>
        info@yourgmail.com
      </li>
      <li>
        <svg viewBox="0 0 24 24" aria-hidden="true"><circle cx="12" cy="12" r="10"/></svg>
        www.yourwebsite.com
      </li>
    </ul>
    <p class="address">Your address, City State, Zip 1234</p>
  </section>

  <section class="card card-brand" aria-label="Business card, brand side">
    <div class="wordmark">
      <span class="wordmark-main">Meridian Service</span>
      <span class="wordmark-sub">Reps</span>
    </div>
    <ul class="social-row" aria-label="Social media links">
      <li></li><li></li><li></li><li></li><li></li><li></li>
    </ul>
  </section>

</main>
</body>
</html>
```